English and Spanish Language School Needs a Business Card

Need a business card design a startup company called Maribel Language School. The company will offer English and Spanish conversational level courses designed to make the learner feel comfortable with grammar and vocabulary. We would like to see a logo with some colour that should communicate learning, growth.

Target Market(s)

Consumers and businesses

Industry/Entity Type

Education

Contact Information for Business Card

TBD

Font styles to use
Serif

Requirements
Must have
• Include the following
• Logo
• Name
• Title
• Cellphone Number
• Office Phone number
• Email address
• Office Address

```html
<!DOCTYPE html>
<html lang="en">
<head>
<meta charset="utf-8">
<title>Maribel Language School – Business Card</title>
<link href="https://fonts.googleapis.com/css2?family=Tinos:wght@400;700&display=swap" rel="stylesheet">
<style>
  :root {
    --page: #e9e7e3;
    --card: #fbfbfb;
    --card-shade: #e4e4e4;
    --red: #d0202f;
    --teal: #1fb5bb;
    --ink-teal: #1aa8ae;
  }
  * { margin: 0; padding: 0; box-sizing: border-box; }
  html, body { width: 1200px; height: 780px; overflow: hidden; }
  body {
    background: var(--page);
    font-family: "Tinos", "Times New Roman", serif;
    position: relative;
  }
  .card {
    position: absolute;
    top: 230px;
    width: 520px;
    height: 300px;
    border-radius: 14px;
    background: var(--card);
    box-shadow: 0 4px 14px rgba(0,0,0,.15);
    overflow: hidden;
  }
  .card--front { left: 50px; }
  .card--back {
    left: 630px;
    background: radial-gradient(circle at 50% 45%, #ffffff 0%, var(--card-shade) 100%);
    display: flex; align-items: center; justify-content: center;
  }
  .edge-band { position: absolute; top: 0; right: 0; width: 24px; height: 100%; }
  .edge-band__red { height: 42%; background: var(--red); }
  .edge-band__teal { height: 58%; background: var(--teal); }

  .brand { display: flex; align-items: center; gap: 10px; }
  .brand__mark { width: 14px; height: 14px; border-radius: 50%; background: var(--teal); flex: none; }
  .brand__name { color: var(--red); font-weight: 700; line-height: .95; }
  .brand__name span { display: block; }
  .brand--front { position: absolute; left: 34px; top: 52px; }
  .brand--front .brand__name { font-size: 44px; }
  .brand--front .brand__name span + span { font-size: 24px; margin-top: 4px; }
  .brand--back .brand__name { font-size: 54px; }
  .brand--back .brand__name span + span { font-size: 29px; margin-top: 6px; }

  .divider {
    position: absolute; left: 34px; top: 176px;
    width: 300px; height: 1px; background: var(--teal);
  }
  .person { position: absolute; right: 50px; top: 30px; text-align: right; }
  .person__name { color: var(--red); font-size: 17px; letter-spacing: .5px; border-bottom: 1px solid var(--teal); padding-bottom: 2px; }
  .person__title { color: var(--ink-teal); font-size: 14px; margin-top: 2px; }
  .address {
    position: absolute; right: 50px; top: 104px;
    text-align: right; color: var(--ink-teal); font-size: 14px; line-height: 1.35;
  }
  .contact { position: absolute; left: 34px; top: 196px; list-style: none; }
  .contact__item {
    display: flex; align-items: center; gap: 8px;
    color: var(--ink-teal); font-size: 14px; line-height: 1; margin-bottom: 7px;
  }
  .contact__icon { width: 16px; height: 16px; flex: none; }
</style>
</head>
<body>

<section class="card card--front" aria-label="Business card front">
  <div class="brand brand--front">
    <div class="brand__name"><span>Maribel</span><span>Language School</span></div>
    <div class="brand__mark"></div>
  </div>

  <div class="divider"></div>

  <div class="person">
    <div class="person__name">DANIEL REYES</div>
    <div class="person__title">Manager</div>
  </div>

  <address class="address">Your Address, 2nd Ste<br>Cedarvale, Texas 1234</address>

  <ul class="contact">
    <li class="contact__item">
      <svg class="contact__icon" viewBox="0 0 16 16"><rect width="16" height="16" rx="2" fill="#d0202f"/><rect x="5" y="3" width="6" height="10" rx="1" fill="none" stroke="#fff" stroke-width="1.3"/><circle cx="8" cy="11" r=".8" fill="#fff"/></svg>
      123 456 7890
    </li>
    <li class="contact__item">
      <svg class="contact__icon" viewBox="0 0 16 16"><rect width="16" height="16" rx="2" fill="#d0202f"/><path d="M4.5 3.5l2 0 1 2.5-1.3 1a6 6 0 0 0 2.8 2.8l1-1.3 2.5 1 0 2c0 .6-.5 1-1 1A8.5 8.5 0 0 1 3.5 4.5c0-.5.4-1 1-1z" fill="#fff"/></svg>
      123 456 7890
    </li>
    <li class="contact__item">
      <svg class="contact__icon" viewBox="0 0 16 16"><rect width="16" height="16" rx="2" fill="#d0202f"/><rect x="3" y="4.5" width="10" height="7" fill="none" stroke="#fff" stroke-width="1.2"/><path d="M3 4.5l5 4 5-4" fill="none" stroke="#fff" stroke-width="1.2"/></svg>
      hello@maribelschool.com
    </li>
  </ul>

  <div class="edge-band">
    <div class="edge-band__red"></div>
    <div class="edge-band__teal"></div>
  </div>
</section>

<section class="card card--back" aria-label="Business card back">
  <div class="brand brand--back">
    <div class="brand__name"><span>Maribel</span><span>Language School</span></div>
    <div class="brand__mark"></div>
  </div>
</section>

</body>
</html>
```